Creation of an elegant and modern turnkey Shopify website

Hello,

We are a new company specializing in the sale of above-ground pools. We want to create a turnkey website, ideally using Shopify. For now, we need a "showcase" site, not an e-commerce platform, with four tabs:

Home Page (an overall presentation of the company)
Our Products (an overview of all the above-ground pools we sell)
Our Projects (a page inspired by Instagram to showcase photos of our future projects)
Contact (a page with all our contact information and a contact form)

We are looking to create a highly visual, elegant, and modern website with vibrant splashes of color. We will provide the text, photos (along with instructions on where to place them on each page), and all other necessary information as attachments.

Thank you in advance for your proposals!

The Brisa Lagoon Team

Target Market(s)

Targeted at Swiss customers (a translator will need to be installed for different languages)

Industry/Entity Type

Sale of customised above-ground pools

Coding

Coded - Design and coding required

Font styles to use
Sans Serif

Colors
0094D4
00A9DD
6FCCEA
C7EBF8
E9F6FB
00AB8E
00BBA5
67D7C9
C6EFE9
E9F9F6

Requirements
Must have
• A stunning, elegant and modern look
Nice to have
• Inspiration from the colors of our logo throughout the site, but in an elegant way
Should not have
• An overly classic look for swimming pool sites

```html
<!DOCTYPE html>
<html lang="en">
<head>
<meta charset="utf-8">
<title>Brisa Lagoon – Contact</title>
<link href="https://fonts.googleapis.com/css2?family=Figtree:wght@300;400;500;600&display=swap" rel="stylesheet">
<style>
:root{
  --aqua:#00e1f0;
  --aqua-soft:#cdf9fc;
  --ink:#111;
  --white:#fff;
  --slate:#5b5a5b;
  --footer:#7a797a;
  --footer-bar:#666566;
  --button-grey:#656465;
  --placeholder:#9a9a9a;
}
*{box-sizing:border-box;margin:0;padding:0}
html,body{width:1200px;height:2498px;overflow:hidden}
body{position:relative;font-family:'Figtree',sans-serif;color:var(--ink);background:var(--white)}
.abs{position:absolute}

/* header */
.site-header{position:absolute;left:0;top:0;width:1200px;height:110px;background:var(--white);z-index:3}
.logo-disc{position:absolute;left:52px;top:-16px;width:216px;height:216px;border-radius:50%;background:var(--white);z-index:4;display:flex;align-items:center;justify-content:center;padding-bottom:60px}
.brand{font-weight:300;font-size:34px;line-height:1;color:var(--aqua);text-align:center;letter-spacing:2px}
.nav-link{position:absolute;top:50px;font-size:15px;font-weight:500;color:var(--ink);text-decoration:none;white-space:nowrap;z-index:4;line-height:18px}
.nav-link.active{color:var(--aqua)}
.nav-underline{position:absolute;left:547px;top:78px;width:61px;height:3px;background:var(--aqua);z-index:4}
.lang-switch{position:absolute;left:1067px;top:37px;width:61px;height:42px;border:1px solid #ddd;border-radius:6px;z-index:4;display:flex;align-items:center;justify-content:center;gap:6px}

/* hero */
.hero{position:absolute;left:0;top:110px;width:1200px;height:702px;
  background:linear-gradient(180deg,#3d7ed4 0%,#8ab8e8 22%,#5a6f86 40%,#4b5a6d 60%,#3f8a2e 78%,#5da83a 100%)}
.hero-title{position:absolute;left:0;width:1300px;top:482px;text-align:center;color:var(--white);font-weight:600;font-size:40px;line-height:45px;letter-spacing:.3px}
.pill{position:absolute;display:flex;align-items:center;justify-content:center;gap:12px;border-radius:30px;font-weight:600;color:var(--white);font-size:16px}
.pill .chev{width:32px;height:32px;border-radius:50%;background:var(--white);display:flex;align-items:center;justify-content:center}
.hero-cta{left:539px;top:641px;width:221px;height:57px;background:var(--aqua)}
.slider-dots{position:absolute;left:600px;top:761px;display:flex;gap:12px;align-items:center}
.slider-dots span{width:11px;height:11px;border-radius:50%;background:#bdbdbd}
.slider-dots span.on{width:28px;height:5px;border-radius:3px;background:var(--white)}

/* intro */
.section-title{position:absolute;left:0;width:1200px;top:902px;text-align:center;font-size:48px;font-weight:500;letter-spacing:.5px}
.title-rule{position:absolute;left:542px;top:972px;width:116px;height:2px;background:var(--ink)}
.intro{position:absolute;left:100px;width:1010px;top:1011px;text-align:center;font-size:30px;line-height:36px;font-weight:400;white-space:nowrap}

/* contact band */
.info-panel{position:absolute;left:0;top:1238px;width:534px;height:791px;background:var(--slate)}
.form-panel{position:absolute;left:534px;top:1238px;width:666px;height:791px;background:var(--aqua-soft)}
.info-icon{position:absolute;left:155px;width:74px;height:74px;border-radius:50%;background:var(--aqua);display:flex;align-items:center;justify-content:center}
.info-text{position:absolute;left:246px;color:var(--white);font-size:19px;line-height:25px}
.info-text strong{font-weight:500;font-size:22px}
.field-label{position:absolute;font-size:14px;font-weight:500;letter-spacing:.2px;color:var(--ink)}
.field{position:absolute;background:var(--white);height:45px;font-size:14px;color:var(--placeholder);padding:14px 14px 0}
.submit{left:729px;top:1863px;width:197px;height:58px;background:var(--button-grey)}
.submit .chev{background:var(--aqua)}

/* footer */
.site-footer{position:absolute;left:0;top:2110px;width:1200px;height:335px;background:var(--footer);color:var(--white)}
.footer-bar{position:absolute;left:0;top:2445px;width:1200px;height:53px;background:var(--footer-bar);color:var(--white)}
.footer-brand{position:absolute;left:90px;top:80px;width:260px;font-size:52px;font-weight:300;line-height:1.2;color:var(--white);text-align:center;letter-spacing:3px}
.col-title{position:absolute;top:66px;font-size:22px;font-weight:400}
.col-title::after{content:"";position:absolute;left:0;top:36px;width:36px;height:2px;background:var(--aqua)}
.quick-links{position:absolute;left:402px;top:146px;list-style:none;font-size:14px;line-height:27px}
.quick-links li::before{content:"›";color:var(--aqua);margin-right:10px;font-size:16px}
.f-icon{position:absolute;left:611px;width:29px;height:29px;border:1px solid var(--aqua);border-radius:3px;display:flex;align-items:center;justify-content:center}
.f-text{position:absolute;left:657px;font-size:13px;line-height:16px}
.newsletter-input{position:absolute;left:886px;top:192px;width:219px;height:35px;background:var(--white);border:1px solid #ccc}
.subscribe{position:absolute;left:886px;top:236px;width:110px;height:34px;background:var(--aqua);color:#333;font-size:12px;display:flex;align-items:center;justify-content:center}
.copyright{position:absolute;left:77px;top:19px;font-size:14px}
.social{position:absolute;top:11px;width:31px;height:31px;border:1px solid var(--aqua);border-radius:4px;background:#4a4a4a}
</style>
</head>
<body>

<header class="site-header">
  <a class="nav-link active" style="left:553px">HOME</a>
  <a class="nav-link" style="left:634px">OUR PRODUCTS</a>
  <a class="nav-link" style="left:790px">OUR PROJECTS</a>
  <a class="nav-link" style="left:940px">CONTACT US</a>
  <div class="nav-underline"></div>
  <div class="lang-switch" aria-label="Language selector">
    <svg width="30" height="19" viewBox="0 0 30 19"><rect width="30" height="19" fill="#1f3f8a"/><rect x="12" width="6" height="19" fill="#fff"/><rect y="6.5" width="30" height="6" fill="#fff"/><rect x="13.5" width="3" height="19" fill="#d2232a"/><rect y="8" width="30" height="3" fill="#d2232a"/></svg>
    <svg width="10" height="7" viewBox="0 0 10 7"><path d="M0 0h10L5 7z" fill="#888"/></svg>
  </div>
</header>
<div class="logo-disc"><div class="brand">BRISA<br>LAGOON</div></div>

<section class="hero" role="img" aria-label="Photo of an above-ground pool with wood-clad walls, steps and a waterfall on a green lawn under a blue sky"></section>
<h1 class="hero-title">TRANSFORM YOUR<br>GARDEN WITH OUR PREMIUM<br>ABOVE-GROUND POOLS!</h1>
<a class="pill hero-cta">OUR PRODUCTS <span class="chev"><svg width="14" height="10" viewBox="0 0 14 10"><path d="M1 1l4 4-4 4M8 1l4 4-4 4" stroke="#00e1f0" stroke-width="2" fill="none"/></svg></span></a>
<div class="slider-dots"><span class="on"></span><span></span><span></span><span></span></div>

<h2 class="section-title">CONTACT US</h2>
<div class="title-rule"></div>
<p class="intro">We would be delighted to advise you. Feel free to reach out to us for<br>any inquiries or to get a personalized quote. We look forward to<br>helping you transform your outdoor space into a true haven of<br>peace and relaxation.</p>

<section class="info-panel">
  <div class="info-icon" style="top:112px"><svg width="28" height="38" viewBox="0 0 28 38"><path d="M14 0C6 0 0 6 0 14c0 10 14 24 14 24s14-14 14-24C28 6 22 0 14 0z" fill="#fff"/><circle cx="14" cy="14" r="5" fill="#00e1f0"/></svg></div>
  <p class="info-text" style="top:108px">BRISA LAGOON<br>Marco Veltri<br>Chemin du Lac 12<br>1820 Vernex</p>
  <div class="info-icon" style="top:296px"><svg width="38" height="38" viewBox="0 0 24 24"><path d="M6.6 10.8a15 15 0 006.6 6.6l2.2-2.2c.3-.3.7-.4 1-.2 1.1.4 2.300.6 3.6.6.6 0 1 .4 1 1V20c0 .6-.4 1-1 1C10.6 21 3 13.4 3 4c0-.6.4-1 1-1h3.5c.6 0 1 .4 1 1 0 1.3.2 2.5.6 3.6.1.3 0 .7-.2 1z" fill="#fff"/></svg></div>
  <p class="info-text" style="top:312px"><strong>CALL US</strong><br>079 000 12 34</p>
  <div class="info-icon" style="top:487px"><svg width="38" height="28" viewBox="0 0 38 28"><rect width="38" height="28" rx="2" fill="#fff"/><path d="M1 2l18 14L37 2M1 27l13-13M37 27L24 14" stroke="#00e1f0" stroke-width="2" fill="none"/></svg></div>
  <p class="info-text" style="top:503px"><strong>EMAIL US</strong><br>hello@brisalagoon.example</p>
</section>

<section class="form-panel"></section>
<label class="field-label" style="left:595px;top:1335px">TELL US YOUR NAME *</label>
<div class="field" style="left:595px;top:1365px;width:223px">First Name</div>
<div class="field" style="left:838px;top:1365px;width:223px">Last Name</div>
<label class="field-label" style="left:595px;top:1439px">ENTER YOUR EMAIL *</label>
<label class="field-label" style="left:842px;top:1439px">ENTER YOUR PHONE NUMBER *</label>
<div class="field" style="left:595px;top:1469px;width:223px">Email</div>
<div class="field" style="left:838px;top:1469px;width:223px">Phone</div>
<label class="field-label" style="left:595px;top:1542px">TYPE OF POOL *</label>
<label class="field-label" style="left:842px;top:1542px">SIZE * (7M X 3M)</label>
<div class="field" style="left:595px;top:1571px;width:219px">Composite Wood Pools
  <svg style="position:absolute;right:14px;top:17px" width="16" height="12" viewBox="0 0 16 12"><path d="M0 0h16L8 12z" fill="#555"/></svg></div>
<div class="field" style="left:843px;top:1571px;width:92px"></div>
<span class="abs" style="left:949px;top:1584px;font-size:15px">X</span>
<div class="field" style="left:969px;top:1571px;width:92px"></div>
<label class="field-label" style="left:595px;top:1646px">MESSAGE *</label>
<div class="field" style="left:595px;top:1675px;width:466px;height:150px">Write us a message</div>
<a class="pill submit">SUBMIT NOW <span class="chev"><svg width="14" height="10" viewBox="0 0 14 10"><path d="M1 1l4 4-4 4M8 1l4 4-4 4" stroke="#fff" stroke-width="2" fill="none"/></svg></span></a>

<footer class="site-footer">
  <div class="footer-brand">BRISA<br>LAGOON</div>
  <h3 class="col-title" style="left:398px">Quick Links</h3>
  <ul class="quick-links"><li>Home</li><li>Our Products</li><li>Our Projects</li><li>Contact Us</li></ul>
  <h3 class="col-title" style="left:611px">Contact Us</h3>
  <div class="f-icon" style="top:142px"><svg width="14" height="14" viewBox="0 0 24 24"><path d="M6.6 10.8a15 15 0 006.6 6.6l2.2-2.2c.3-.3.7-.4 1-.2 1.1.4 2.3.6 3.6.6.6 0 1 .4 1 1V20c0 .6-.4 1-1 1C10.6 21 3 13.4 3 4c0-.6.4-1 1-1h3.5c.6 0 1 .4 1 1 0 1.3.2 2.5.6 3.6.1.3 0 .7-.2 1z" fill="#fff"/></svg></div>
  <p class="f-text" style="top:142px">CALL US<br>079 000 12 34</p>
  <div class="f-icon" style="top:190px"><svg width="12" height="9" viewBox="0 0 12 9"><rect width="12" height="9" fill="#fff"/><path d="M0 1l6 4 6-4" stroke="#7a797a" fill="none"/></svg></div>
  <p class="f-text" style="top:190px">EMAIL US<br>hello@brisalagoon.example</p>
  <div class="f-icon" style="top:238px"><svg width="10" height="14" viewBox="0 0 28 38"><path d="M14 0C6 0 0 6 0 14c0 10 14 24 14 24s14-14 14-24C28 6 22 0 14 0z" fill="#fff"/></svg></div>
  <p class="f-text" style="top:238px">Marco Veltri<br>Chemin du Lac 12<br>1820 Vernex</p>
  <h3 class="col-title" style="left:886px;top:64px">Our Newsletter</h3>
  <p class="abs" style="left:886px;top:146px;width:230px;font-size:13px;line-height:18px">Subscribe our newsletter to get the latest news.</p>
  <div class="newsletter-input"></div>
  <div class="subscribe">SUBSCRIBE</div>
</footer>
<div class="footer-bar">
  <p class="copyright">Copyright © 2024 All Rights Reserved By Company name</p>
  <span class="social" style="left:989px" aria-label="Social link"></span>
  <span class="social" style="left:1024px" aria-label="Social link"></span>
  <span class="social" style="left:1059px" aria-label="Social link"></span>
  <span class="social" style="left:1094px" aria-label="Social link"></span>
</div>

</body>
</html>
```